Bahamas Pharmacy needs Flyer to Promote "Blood Pressure Tracking Service"

We need a double sided flyer design 5.5" x 8.5" (redesign) to promote a "Blood Pressure Tracking Service". Persons that have a card will be able to track their blood pressure online through a secure online blood pressure tracker. Clients of Coral Tide Pharmacy will be to test themselves--so information is confidential. Test Regularly - their information is stored up to 30 readings. Share the printed results. Flyer must contain endorsement logos of Silver Reef Cardiac Association Flyer and Palm Crest Glucose Association. The final design should communicate responsible tracking of health of elders and parents look clean, crisp, elegant modern yet simplistic. Any imagery should be friendly to the mixed-race demographic of the Bahamas. Contain imagery on either side of "Chatterloop and Pipsqueak"

Target Market(s)

Families

Industry/Entity Type

Health

Font styles to use
Sans Serif

Colors
0255a3
9ccb3b
ffffff
ec2027

Requirements
Must have
• Images of Happy African-American or Mixed-Race Family, Similar Aesthetic to "Perks Circle" flyer
Nice to have
• Imagery of Nurse taking blood pressure monitor, please see example of imagery type to be used.
Should not have
• Too much text, Small Imagery,

```html
<!DOCTYPE html>
<html lang="en">
<head>
<meta charset="utf-8">
<title>Coral Tide Pharmacy – Blood Pressure Tracking Service</title>
<link rel="stylesheet" href="https://fonts.googleapis.com/css2?family=Open+Sans:wght@400;600;700&family=Arvo:wght@400;700&display=swap">
<style>
  :root {
    --backdrop: #e9e6e1;
    --paper: #ffffff;
    --forest: #1e4d2b;
    --leaf: #2f9a3c;
    --lime: #9ccb3b;
    --coral-red: #c4161c;
    --ink: #3a3a3a;
    --mist: #e7e7e7;
  }
  * { box-sizing: border-box; margin: 0; padding: 0; }
  html, body { width: 840px; height: 1200px; overflow: hidden; }
  body { background: var(--backdrop); font-family: "Open Sans", Arial, sans-serif; position: relative; }
  .flyer { position: absolute; left: 91px; top: 90px; width: 659px; height: 1020px; background: var(--paper); overflow: hidden; }

  .brand { position: absolute; left: 0; top: 0; width: 100%; height: 146px; }
  .brand-mark { position: absolute; left: 110px; top: 46px; width: 44px; height: 44px; border-radius: 50%; background: var(--leaf); }
  .brand-name { position: absolute; left: 170px; top: 44px; font-size: 31px; font-weight: 600; font-variant: small-caps; color: var(--coral-red); letter-spacing: .5px; white-space: nowrap; }
  .tagline { position: absolute; left: 222px; top: 106px; font-size: 18px; color: var(--leaf); white-space: nowrap; }
  .tagline strong { font-style: italic; font-weight: 700; }

  .stripe { position: absolute; left: 0; width: 100%; height: 11px; display: flex; }
  .stripe span { flex: 1; background: var(--forest); }
  .stripe span:nth-child(even) { background: var(--leaf); }
  .stripe-top { top: 146px; }
  .stripe-mid { top: 410px; }
  .stripe-foot { top: 1005px; height: 15px; }

  .hero { position: absolute; left: 0; top: 157px; width: 100%; height: 253px;
    background: radial-gradient(circle at 70% 40%, #d8ecb0 0%, #8cc54a 35%, #3f8f2e 75%, #2a6e22 100%); }
  .hero-cta { position: absolute; right: 8px; top: 308px; text-align: center; white-space: nowrap; }
  .hero-cta .shout { font-family: "Arvo", Georgia, serif; font-weight: 700; font-size: 34px; color: var(--coral-red); line-height: 1; text-shadow: 0 0 3px #fff, 0 0 3px #fff; }
  .hero-cta .sub { font-family: "Arvo", Georgia, serif; font-weight: 700; font-size: 20px; color: #fff; text-shadow: 1px 1px 2px #1b3d14; margin-top: 4px; }

  .service-title { position: absolute; left: 0; top: 470px; width: 100%; text-align: center; }
  .service-title h1 { font-family: "Arvo", Georgia, serif; font-weight: 700; font-size: 38px; color: var(--forest); line-height: 1.1; }
  .service-title h2 { font-family: "Arvo", Georgia, serif; font-weight: 700; font-size: 23px; color: var(--coral-red); margin-top: 4px; }

  .features { position: absolute; left: 20px; top: 570px; width: 617px; height: 237px; background: var(--forest); padding: 18px 12px 0 50px; color: #fff; }
  .features::before, .features::after { content: ""; position: absolute; left: 297px; border-left: 14px solid transparent; border-right: 14px solid transparent; }
  .features::before { top: -14px; border-bottom: 14px solid var(--forest); }
  .features::after { bottom: -14px; border-top: 14px solid var(--forest); }
  .features li { list-style: none; position: relative; font-size: 16px; line-height: 26px; margin-bottom: 8px; }
  .features li::before { content: ""; position: absolute; left: -30px; top: 8px; width: 11px; height: 11px; border-radius: 50%; background: var(--coral-red); }

  .address { position: absolute; left: 21px; top: 835px; font-size: 15.5px; color: var(--ink); line-height: 23px; font-style: normal; }
  .phones { position: absolute; left: 17px; top: 910px; display: flex; align-items: center; gap: 8px; font-size: 18px; font-weight: 700; color: var(--forest); white-space: nowrap; }
  .phones svg { width: 22px; height: 20px; }
  .phones .gap { width: 10px; }

  .social { position: absolute; left: 466px; top: 843px; width: 172px; height: 72px; background: var(--mist); border-radius: 12px; padding: 10px 8px; font-size: 12.5px; color: var(--ink); }
  .social::after { content: ""; position: absolute; right: 0; bottom: -14px; border-left: 40px solid transparent; border-top: 14px solid var(--mist); }
  .social p { display: flex; align-items: center; gap: 6px; height: 26px; white-space: nowrap; }
  .social i { flex: none; width: 16px; height: 16px; background: #4a6ea8; border-radius: 3px; }
  .social p + p i { background: #43b3e0; }

  .web-band { position: absolute; left: 0; top: 957px; width: 100%; height: 48px; background: var(--coral-red); color: #fff; text-align: center; font-size: 26px; font-weight: 700; line-height: 48px; }
</style>
</head>
<body>
<main class="flyer">
  <header class="brand">
    <span class="brand-mark"></span>
    <div class="brand-name">Coral Tide Pharmacy</div>
    <p class="tagline">Healthier choices, <strong>Lower</strong> Prices</p>
  </header>

  <div class="stripe stripe-top"><span></span><span></span><span></span><span></span><span></span><span></span><span></span><span></span></div>

  <section class="hero" role="img" aria-label="Photo of a smiling family of four sitting together on a soft green bokeh background, with a blood pressure smart card shown at the upper right"></section>
  <div class="hero-cta">
    <div class="shout">Be Smart!</div>
    <div class="sub">Track Your Blood Pressure</div>
  </div>

  <div class="stripe stripe-mid"><span></span><span></span><span></span><span></span><span></span><span></span><span></span><span></span></div>

  <div class="service-title">
    <h1>Blood Pressure</h1>
    <h2>Tracking Service</h2>
  </div>

  <ul class="features">
    <li>View your results online through a secure online blood pressure tracker<br>(see reverse for instructions)</li>
    <li>Test yourself on the blood pressure kiosk - simple and easy</li>
    <li>Test regularly-the card will store 30 readings and the ticket will print the average of your last 10 results and pulse rate.</li>
    <li>Share the printed results with your pharmacist/doctor to help<br>manage your health!</li>
  </ul>

  <address class="address">
    14 Harbour Row Drive,<br>
    Seagrape Plaza, P.O.Box F 58120,<br>
    Freeport, Grand Bahama, Bahamas
  </address>

  <div class="phones">
    <svg viewBox="0 0 22 20" aria-hidden="true"><rect x="5" y="1" width="12" height="7" fill="none" stroke="#1e4d2b" stroke-width="2"/><rect x="1" y="8" width="20" height="10" rx="2" fill="#1e4d2b"/><rect x="5" y="11" width="12" height="2" fill="#fff"/></svg>
    <span>(242) 555 0148</span>
    <span class="gap"></span>
    <svg viewBox="0 0 22 20" aria-hidden="true"><path d="M6 2c1 0 3 4 3 5s-2 1-2 2 3 5 4 5 1-2 2-2 5 2 5 3-2 3-4 3C9 18 3 11 3 6c0-2 2-4 3-4z" fill="none" stroke="#1e4d2b" stroke-width="1.8"/></svg>
    <span>(242) 555 0136 / 7</span>
  </div>

  <aside class="social">
    <p><i></i>Follow Us on Chatterloop</p>
    <p><i></i>Follow Us on Pipsqueak</p>
  </aside>

  <footer class="web-band">www.coraltidepharmacy.com</footer>
  <div class="stripe stripe-foot"><span></span><span></span><span></span><span></span><span></span><span></span><span></span><span></span></div>
</main>
</body>
</html>
```